automotive repair and collision repair shop card

our company is called K.L Motor service we are a automotive repair company
we also do government inspections. the company information is on the cards. I would like you to use my new logo and create a new card and use the information from my old card. Good Luck!!

Industry/Entity Type

Car Repair

Contact Information for Business Card

Address: #417-18842 52 Ave, Surrey, BC V5K 8R3
Phone:(604) 555-0187
fax 604 555 0193
website www.klmotorworks.example

Font styles to use
Serif
Sans Serif

Requirements
Must have
• all the information
Should not have
• the owner and there name

```html
<!DOCTYPE html>
<html lang="en">
<head>
<meta charset="utf-8">
<title>K.L Motor service – business card</title>
<link rel="stylesheet" href="https://fonts.googleapis.com/css2?family=Pathway+Gothic+One&display=swap">
<style>
  :root {
    --backdrop: #e6e4e1;
    --card-white: #f4f4f4;
    --card-light: #dcdcdc;
    --ink: #151515;
    --panel-grey: #6e6e6e;
    --band-black: #0c0c0c;
    --text-light: #f2f2f2;
    --muted: #555555;
  }
  * { margin: 0; padding: 0; box-sizing: border-box; }
  html, body { width: 1200px; height: 902px; overflow: hidden; background: var(--backdrop); }
  .sheet { position: relative; width: 1200px; height: 902px; }
  .card {
    position: absolute; left: 320px; width: 560px; height: 320px;
    background: linear-gradient(180deg, var(--card-white) 0%, var(--card-light) 100%);
    box-shadow: 0 8px 24px rgba(0,0,0,.18);
    overflow: hidden;
  }
  .card--front { top: 100px; }
  .card--back { top: 482px; }
  .card__shapes { position: absolute; inset: 0; }
  .brand { position: absolute; display: flex; align-items: center; gap: 12px; }
  .brand__mark { width: 22px; height: 22px; border-radius: 50%; background: var(--ink); }
  .brand__name {
    font-family: "Pathway Gothic One", sans-serif; color: var(--ink);
    text-transform: uppercase; letter-spacing: 1px; line-height: 1; white-space: nowrap;
  }
  .tagline {
    position: absolute; font-family: "Pathway Gothic One", sans-serif;
    color: var(--muted); letter-spacing: .5px; white-space: nowrap;
  }
  .card--front .brand { left: 0; right: 0; top: 100px; justify-content: center; }
  .card--front .brand__name { font-size: 46px; }
  .card--front .tagline { right: 92px; top: 152px; font-size: 17px; }
  .card--back .brand { left: 120px; top: 70px; }
  .card--back .brand__mark { width: 16px; height: 16px; }
  .card--back .brand__name { font-size: 32px; }
  .card--back .tagline { left: 310px; top: 108px; font-size: 13px; }
  .contacts {
    position: absolute; left: 22px; top: 220px; list-style: none;
    font-family: "Pathway Gothic One", sans-serif; font-size: 14px; color: var(--text-light);
  }
  .contacts li { display: flex; align-items: center; gap: 9px; height: 17px; white-space: nowrap; }
  .contacts svg { width: 12px; height: 12px; flex: none; }
</style>
</head>
<body>
<main class="sheet">

  <section class="card card--front" aria-label="Card front">
    <svg class="card__shapes" viewBox="0 0 560 320" aria-hidden="true">
      <polygon points="300,238 560,226 560,252 300,252" fill="var(--panel-grey)"/>
      <polygon points="0,252 560,252 560,320 0,320" fill="var(--band-black)"/>
    </svg>
    <div class="brand"><span class="brand__mark"></span><span class="brand__name">K.L Motor service</span></div>
    <p class="tagline">One Stop Repair Shop</p>
  </section>

  <section class="card card--back" aria-label="Card back">
    <svg class="card__shapes" viewBox="0 0 560 320" aria-hidden="true">
      <polygon points="250,148 560,148 560,320 440,320 478,250" fill="var(--panel-grey)"/>
      <polygon points="0,212 250,148 472,252 430,320 0,320" fill="var(--band-black)" stroke="#ffffff" stroke-width="3"/>
    </svg>
    <div class="brand"><span class="brand__mark"></span><span class="brand__name">K.L Motor service</span></div>
    <p class="tagline">One Stop Repair Shop</p>

    <ul class="contacts">
      <li><svg viewBox="0 0 12 12"><rect width="12" height="12" fill="#fff"/><path d="M3 2.5l1.6 0 .6 2-1 .7a5 5 0 0 0 2.6 2.6l.7-1 2 .6v1.6A1 1 0 0 1 8.5 10 6.5 6.5 0 0 1 2 3.5a1 1 0 0 1 1-1z" fill="#111"/></svg>(604) 555-0187</li>
      <li><svg viewBox="0 0 12 12"><rect width="12" height="12" fill="#fff"/><rect x="2.5" y="4" width="7" height="5" fill="#111"/><rect x="4" y="2" width="4" height="2.5" fill="#111"/></svg>604 555 0193</li>
      <li><svg viewBox="0 0 12 12"><rect width="12" height="12" fill="#fff"/><circle cx="6" cy="6" r="3.5" fill="none" stroke="#111" stroke-width="1.2"/><line x1="2.5" y1="6" x2="9.5" y2="6" stroke="#111"/></svg>www.klmotorworks.example</li>
      <li><svg viewBox="0 0 12 12"><rect width="12" height="12" fill="#fff"/><rect x="2.5" y="3.5" width="7" height="5" fill="none" stroke="#111"/><path d="M2.5 3.5L6 6.5 9.5 3.5" fill="none" stroke="#111"/></svg>info@klmotorworks.example</li>
      <li><svg viewBox="0 0 12 12"><rect width="12" height="12" fill="#fff"/><path d="M6 10.5S3 7 3 5a3 3 0 0 1 6 0c0 2-3 5.5-3 5.5z" fill="#111"/><circle cx="6" cy="5" r="1" fill="#fff"/></svg>#417-18842 52 Ave, Surrey, BC V5K 8R3</li>
    </ul>
  </section>

</main>
</body>
</html>
```